Professional Package for CPA Firm

We would like a stationery design for our new CPA Firm based in Atlanta, GA called 'Vale 8'. We work with investors to help grow investments, tax free. We would like the design to have a professional/minimal look with a 'wow' factor. We need 9.5″ x 4.125″, 9x12, and 10x13 mailing envelopes, business cards, and a letterhead. We have a logo that is already complete. For the letterhead, we would like to have space to put credentials at the bottom of the page

Industry/Entity Type

CPA, Accounting

```html
<!DOCTYPE html>
<html lang="en">
<head>
<meta charset="UTF-8">
<title>Vale 8 — Business Card</title>
<link href="https://fonts.googleapis.com/css2?family=Montserrat:wght@600&family=Open+Sans:wght@400;600&display=swap" rel="stylesheet">
<style>
  :root {
    --stage: #2a2b2e;
    --card-navy: #0f3452;
    --teal: #2bb7c2;
    --coral: #f2545b;
    --white: #ffffff;
    --silver: #c9ccd1;
  }
  * { margin: 0; padding: 0; box-sizing: border-box; }
  html, body {
    width: 1200px;
    height: 874px;
    overflow: hidden;
    background: var(--stage);
    font-family: "Open Sans", Arial, sans-serif;
  }
  .stage {
    position: relative;
    width: 1200px;
    height: 874px;
  }
  .card {
    position: absolute;
    left: 290px;
    width: 620px;
    height: 360px;
    background: var(--card-navy);
    border-radius: 18px;
  }
  .card--front { top: 40px; }
  .card--back { top: 474px; }

  .brand {
    display: flex;
    align-items: center;
    gap: 14px;
    font-family: "Montserrat", Arial, sans-serif;
    font-weight: 600;
    letter-spacing: 4px;
  }
  .brand__mark {
    width: 22px;
    height: 22px;
    background: var(--coral);
    border-radius: 3px;
  }
  .card--front .brand {
    position: absolute;
    inset: 0;
    justify-content: center;
    font-size: 58px;
    color: var(--silver);
  }
  .card--back .brand {
    position: absolute;
    right: 54px;
    top: 88px;
    font-size: 40px;
    color: var(--white);
  }
  .card--back .brand__mark { width: 16px; height: 16px; }

  .person {
    position: absolute;
    left: 44px;
    top: 150px;
  }
  .person__name {
    font-size: 22px;
    font-weight: 400;
    letter-spacing: 0.5px;
    color: var(--teal);
    text-transform: uppercase;
  }
  .person__title {
    font-size: 15px;
    color: var(--coral);
    margin-top: -2px;
  }
  .divider {
    position: absolute;
    left: 40px;
    right: 54px;
    top: 212px;
    height: 1px;
    background: var(--teal);
  }
  .contact {
    position: absolute;
    left: 44px;
    top: 226px;
    list-style: none;
  }
  .contact__item {
    display: flex;
    align-items: center;
    gap: 10px;
    font-size: 15px;
    line-height: 22px;
    color: var(--white);
  }
  .contact__icon { width: 12px; height: 12px; flex: none; }
  .address {
    position: absolute;
    right: 54px;
    bottom: 40px;
    text-align: right;
    font-size: 15px;
    line-height: 22px;
    color: var(--white);
  }
</style>
</head>
<body>
<main class="stage">
  <section class="card card--front" aria-label="Card front">
    <div class="brand"><span class="brand__mark"></span><span class="brand__name">VALE 8</span></div>
  </section>

  <section class="card card--back" aria-label="Card back">
    <div class="person">
      <h1 class="person__name">Daniel Carter</h1>
      <p class="person__title">President</p>
    </div>
    <div class="divider"></div>
    <ul class="contact">
      <li class="contact__item">
        <svg class="contact__icon" viewBox="0 0 12 12"><path d="M2.5 1 L4.5 1 L5.2 3.6 L3.9 4.6 Q5 7 7.4 8.1 L8.4 6.8 L11 7.5 L11 9.5 Q10.5 11 9 11 Q1 10 1 3 Q1 1.5 2.5 1Z" fill="var(--coral)"/></svg>
        404-555-0182
      </li>
      <li class="contact__item">
        <svg class="contact__icon" viewBox="0 0 12 12"><rect x="3" y="0.8" width="6.4" height="10.4" rx="1" fill="none" stroke="var(--coral)" stroke-width="1.3"/><rect x="5.4" y="9" width="1.6" height="1" fill="var(--coral)"/></svg>
        404-555-0147
      </li>
      <li class="contact__item">
        <svg class="contact__icon" viewBox="0 0 12 12"><rect x="0.5" y="2.2" width="11" height="7.6" rx="1" fill="var(--coral)"/><path d="M0.8 2.6 L6 6.6 L11.2 2.6" fill="none" stroke="var(--card-navy)" stroke-width="1"/></svg>
        hello@vale8.com
      </li>
    </ul>
    <div class="brand"><span class="brand__mark"></span><span class="brand__name">VALE 8</span></div>
    <address class="address" style="font-style:normal">
      1240 Linden Court<br>
      Atlanta, Georgia 30309<br>
      www.vale8.com
    </address>
  </section>
</main>
</body>
</html>
```